Business Name: DM Space Arranging Pty Ltd

Business Type: Professional Home Styling and Minor Renovation Business

Logo: Attached is the logo that has been created.
I always envisaged the logo in the middle of the business card with my full name underneath it.

Marnie Tulloch B.Com LMR HTV
Property Stylist & Project Manager

Include dot points of services
Staging Houses for Sale
Minor Home Renovations
Home Styling & Project Management
Re-Designing Living Spaces to Aid the Disabled

Somewhere on the card I would like to incorporate
"Property Styling and Cosmetic Renovations"

Colour Scheme:
Gloss black business card, with white and then
Gold or Silver as the highlight colours.

Incorporate a small amount of yellow only if possible to make it pop. If this really doesn’t work it doesn’t have to be used. Also l like the colour teal if that needs to be used as a contrast colour.

Feel/Themes
• I love antique chairs, regal expensive looking furniture mixed with modern homes (this is the unique style I want to sell) antique and modern mix that looks high class as well as modern and fresh, targeting an executive market.
• I want to use an orchid as a trademark throughout the course of my work, not sure if this can somehow be incorporated? Also really like crowns to give that regal/antique feel and then something else to give that modern twist (I don’t know what the something else could be)
• Wall Paper Look (on a portion of it not all of it, like a French look)
• Overall feel - A very deluxe and professional feel with a little bit of creative flare.

I hope this helps create a bit of a picture.

Is it ok that I call you tomorrow morning? My mobile number is 0438 926 574 if you have any questions for me in the meantime.

Target Market(s)

High Quality Executive Market - People selling homes

Industry/Entity Type

Business

Contact Information for Business Card

Include dot points of services:
Staging Houses for Sale
Minor Home Renovations

Font styles to use
Serif
Script

Colors
33b8a4
fbed22

Requirements
Must have
• Marnie Tulloch B.Com LMR HTV
• Property Stylist & Project Manager
• LMR and HTV Logos on the card
• "Dramatically increase the value of your property"
Nice to have
• Colour Scheme:
• Gloss black business card, with white and then
• Gold or Silver as the highlight colours.
• Incorporate a small amount of yellow only if possible to make it pop. If this really doesn’t work it doesn’t have to be used. Also l like the colour teal if that needs to be used as a contrast colour.
• Also like teal as a highlight colour.

```html
<!DOCTYPE html>
<html lang="en">
<head>
<meta charset="utf-8">
<title>DM Space Arranging Pty Ltd — Business Card</title>
<link rel="stylesheet" href="https://fonts.googleapis.com/css2?family=Great+Vibes&family=Old+Standard+TT:wght@400&display=swap">
<style>
  :root {
    --backdrop: #3a3a3c;
    --card: #ffffff;
    --ink: #1b1b1b;
    --black: #0d0d0d;
    --gold: #b8892e;
    --faint: #eeeeee;
    --white: #ffffff;
  }
  html, body {
    margin: 0;
    width: 1200px;
    height: 852px;
    overflow: hidden;
    background: var(--backdrop);
  }
  .stage { position: relative; width: 1200px; height: 852px; }

  .card {
    position: absolute;
    width: 520px;
    height: 296px;
    background: var(--card);
    border-radius: 14px;
    overflow: hidden;
    font-family: "Old Standard TT", Georgia, serif;
    color: var(--ink);
  }
  .card--front { left: 80px; top: 110px; }
  .card--back  { left: 600px; top: 450px; }

  .card__art { position: absolute; inset: 0; width: 520px; height: 296px; }

  .flourish {
    position: absolute;
    width: 230px;
    height: 80px;
    border-radius: 40px;
    background: radial-gradient(ellipse at center, var(--faint) 0%, rgba(238,238,238,0) 70%);
  }

  .wordmark {
    position: absolute;
    text-align: center;
    color: var(--gold);
    font-size: 15px;
    letter-spacing: 2.5px;
    text-transform: uppercase;
    line-height: 1;
    padding: 7px 0;
    border-top: 1px solid var(--ink);
    border-bottom: 1px solid var(--ink);
    white-space: nowrap;
  }

  .services {
    position: absolute;
    left: 148px;
    top: 146px;
    margin: 0;
    padding: 0;
    list-style: none;
    font-size: 12px;
    line-height: 18px;
    white-space: nowrap;
  }
  .services__item::before { content: "» "; }
  .services__row { display: flex; gap: 16px; }

  .badges { position: absolute; left: 18px; top: 184px; width: 112px; height: 78px; }
  .badge { position: absolute; }
  .badge--top { left: 0; top: 0; width: 80px; height: 38px; background: #2a2a2a; }
  .badge--seal { left: 80px; top: 0; width: 32px; height: 38px; background: var(--white); border: 1px solid #bbb; box-sizing: border-box; }
  .badge--bottom { left: 0; top: 38px; width: 112px; height: 40px; background: var(--black); }

  .person { position: absolute; left: 34px; top: 112px; }
  .person__name {
    font-family: "Great Vibes", cursive;
    font-size: 30px;
    line-height: 36px;
    margin: 0 0 2px;
    font-weight: 400;
  }
  .person__role { margin: 0; font-size: 12.5px; line-height: 15px; }

  .contact {
    position: absolute;
    left: 34px;
    top: 208px;
    margin: 0;
    padding: 0;
    list-style: none;
    font-size: 13px;
    line-height: 17px;
  }
  .contact li { display: flex; align-items: center; gap: 9px; }
  .contact svg { width: 12px; height: 12px; fill: var(--ink); }

  .tagline {
    position: absolute;
    right: 14px;
    top: 176px;
    margin: 0;
    color: var(--white);
    font-size: 12.5px;
    line-height: 17px;
    text-align: left;
    white-space: nowrap;
  }
</style>
</head>
<body>
<main class="stage">

  <section class="card card--front" aria-label="Card front">
    <svg class="card__art" viewBox="0 0 520 296" aria-hidden="true">
      <defs>
        <linearGradient id="goldBand" x1="0" y1="0" x2="1" y2="0">
          <stop offset="0" stop-color="#8a6218"/>
          <stop offset="0.45" stop-color="#e9c56b"/>
          <stop offset="0.75" stop-color="#b8892e"/>
          <stop offset="1" stop-color="#f3d98c"/>
        </linearGradient>
      </defs>
      <path d="M0 287 C 200 281, 380 251, 520 196 L520 205 C 380 260, 200 290, 0 296 Z" fill="#0d0d0d"/>
      <path d="M0 296 C 200 290, 380 260, 520 205 L520 214 C 380 268, 200 296, 0 296 Z" fill="url(#goldBand)"/>
    </svg>

    <div class="flourish" role="img" aria-label="Faint ornamental flourish behind the name" style="left:160px; top:30px;"></div>
    <div class="wordmark" style="left:95px; top:62px; width:330px;">DM Space Arranging Pty Ltd</div>

    <ul class="services">
      <li class="services__row"><span class="services__item">Staging Homes for Sale</span><span class="services__item">Minor Home Renovations</span></li>
      <li class="services__item">Source Furnishings &amp; Accessories</li>
      <li class="services__item">Re-Designing Rooms for the Disabled</li>
      <li class="services__item">Home Styling, Project &amp; Budget Management</li>
    </ul>

    <div class="badges" aria-label="Professional membership badges">
      <div class="badge badge--top"></div>
      <div class="badge badge--seal"></div>
      <div class="badge badge--bottom"></div>
    </div>
  </section>

  <section class="card card--back" aria-label="Card back">
    <svg class="card__art" viewBox="0 0 520 296" aria-hidden="true">
      <defs>
        <linearGradient id="goldSwoosh" x1="0" y1="1" x2="1" y2="0">
          <stop offset="0" stop-color="#8a6218"/>
          <stop offset="0.4" stop-color="#e9c56b"/>
          <stop offset="0.7" stop-color="#b8892e"/>
          <stop offset="1" stop-color="#f3d98c"/>
        </linearGradient>
      </defs>
      <path d="M520 80 C 430 100, 385 140, 362 185 C 340 240, 310 280, 260 296 L520 296 Z" fill="#0d0d0d"/>
      <path d="M0 290 C 150 284, 280 268, 330 222 C 356 190, 372 120, 505 84 L508 88 C 380 124, 366 196, 340 230 C 290 276, 150 292, 0 296 Z" fill="url(#goldSwoosh)"/>
      <path d="M0 276 C 150 272, 270 256, 316 214 C 342 184, 356 124, 480 92 L482 95 C 362 128, 350 190, 324 220 C 276 262, 150 280, 0 280 Z" fill="url(#goldSwoosh)"/>
    </svg>

    <div class="flourish" role="img" aria-label="Faint ornamental flourish behind the name" style="left:270px; top:16px;"></div>
    <div class="wordmark" style="left:256px; top:44px; width:250px; font-size:11.5px; letter-spacing:1.5px;">DM Space Arranging Pty Ltd</div>

    <div class="person">
      <h1 class="person__name">Marnie Tulloch</h1>
      <p class="person__role">B.Com LMR HTV<br>Property Stylist &amp;<br>Project Manager</p>
    </div>

    <ul class="contact">
      <li>
        <svg viewBox="0 0 24 24" aria-hidden="true"><path d="M6.6 10.8a15 15 0 0 0 6.6 6.6l2.2-2.2c.3-.3.7-.4 1-.2 1.1.4 2.3.6 3.6.6.6 0 1 .4 1 1V20c0 .6-.4 1-1 1A17 17 0 0 1 3 4c0-.6.4-1 1-1h3.5c.6 0 1 .4 1 1 0 1.3.2 2.5.6 3.6.1.3 0 .7-.2 1z"/></svg>
        <span>00 00 000 00 0</span>
      </li>
      <li>
        <svg viewBox="0 0 24 24" aria-hidden="true"><path d="M2 5h20v14H2z M2 5l10 8 10-8" stroke="#fff" stroke-width="1.5"/></svg>
        <span>yourname@yourwebsite.com</span>
      </li>
      <li>
        <svg viewBox="0 0 24 24" aria-hidden="true"><circle cx="12" cy="12" r="10"/></svg>
        <span>www.yourwebsite.com</span>
      </li>
    </ul>

    <p class="tagline">Dramatically Increase<br>the Value of Your Home</p>
  </section>

</main>
</body>
</html>
```